New Business Card Design Project

Need a design that will create an impact / strong impression towards our clients for our business. We are in the lighting business and we do lighting retrofits for large commercial to industrial clientele.

Target Market(s)

Lighting Industry

Industry/Entity Type

Business

Font styles to use
Other font styles liked:
• we would like to use the font on our logo, not sure what it is though..

Requirements
Must have
• Our logo.
Nice to have
• We are open to suggestions that have to do with lighting.

```html
<!DOCTYPE html>
<html lang="en">
<head>
<meta charset="utf-8">
<title>Brightway Retrofit Co. — Business Card</title>
<link href="https://fonts.googleapis.com/css2?family=Source+Sans+3:wght@400;600&display=swap" rel="stylesheet">
<style>
  :root {
    --stage: #000000;
    --card-white: #ffffff;
    --green-deep: #0f4d1c;
    --green-mid: #0d8a3a;
    --green-bright: #4cba4f;
    --green-brand: #1b5e22;
    --text-light: #ffffff;
  }
  html, body {
    margin: 0;
    padding: 0;
    width: 1200px;
    height: 900px;
    overflow: hidden;
    background: var(--stage);
    font-family: "Source Sans 3", "Myriad Pro", Arial, sans-serif;
  }
  .stage {
    position: relative;
    width: 1200px;
    height: 900px;
  }
  .card {
    position: absolute;
    top: 271px;
    width: 457px;
    height: 281px;
    border-radius: 14px;
    overflow: hidden;
  }
  .card--front { left: 137px; }
  .card--back {
    left: 626px;
    width: 458px;
    background: var(--card-white);
    display: flex;
    align-items: center;
    justify-content: center;
  }
  .front-art {
    position: absolute;
    inset: 0;
    background:
      linear-gradient(90deg, #2d6a2a 0%, #2d6a2a 15%, transparent 15%),
      linear-gradient(135deg, var(--green-bright) 0%, var(--green-mid) 45%, var(--green-deep) 100%);
  }
  .contact {
    position: absolute;
    left: 249px;
    top: 63px;
    color: var(--text-light);
  }
  .contact__name {
    margin: 0;
    font-size: 19px;
    font-weight: 600;
    line-height: 1.1;
  }
  .contact__role {
    margin: 1px 0 0;
    font-size: 13px;
    line-height: 1.2;
  }
  .contact__address {
    margin: 13px 0 0;
    font-size: 13px;
    line-height: 16px;
  }
  .contact__list {
    list-style: none;
    margin: 11px 0 0;
    padding: 0;
    font-size: 13px;
    line-height: 16.5px;
  }
  .contact__list li {
    display: flex;
    align-items: center;
    gap: 6px;
  }
  .contact__list svg {
    width: 10px;
    height: 10px;
    fill: var(--text-light);
  }
  .brand {
    display: flex;
    align-items: center;
    gap: 12px;
    margin-top: -12px;
  }
  .brand__mark {
    width: 26px;
    height: 26px;
    background: var(--green-brand);
  }
  .brand__name {
    font-size: 27px;
    font-weight: 600;
    color: var(--green-brand);
    letter-spacing: 0.2px;
  }
</style>
</head>
<body>
<main class="stage">
  <section class="card card--front">
    <div class="front-art" role="img" aria-label="Abstract green geometric background with stepped vertical panels"></div>
    <div class="contact">
      <h1 class="contact__name">Daniel Brooks</h1>
      <p class="contact__role">Managing Director</p>
      <p class="contact__address">12345, Address Goes Here<br>Country Name, 123456.</p>
      <ul class="contact__list">
        <li><svg viewBox="0 0 24 24" aria-hidden="true"><path d="M6.6 10.8a15 15 0 0 0 6.6 6.6l2.2-2.2c.3-.3.7-.4 1-.2 1.1.4 2.3.6 3.6.6.6 0 1 .4 1 1V20c0 .6-.4 1-1 1A17 17 0 0 1 3 4c0-.6.4-1 1-1h3.5c.6 0 1 .4 1 1 0 1.3.2 2.5.6 3.6.1.3 0 .7-.2 1z"/></svg>044-123 456 789</li>
        <li><svg viewBox="0 0 24 24" aria-hidden="true"><path d="M2 5h20v14H2z M2 5l10 7 10-7" /></svg>hello@brightwayretro.com</li>
        <li><svg viewBox="0 0 24 24" aria-hidden="true"><path d="M10 14a4 4 0 0 1 0-5.7l3-3a4 4 0 0 1 5.7 5.7l-1.5 1.5-1.4-1.4 1.5-1.5a2 2 0 0 0-2.9-2.9l-3 3a2 2 0 0 0 0 2.9zm4-4a4 4 0 0 1 0 5.7l-3 3a4 4 0 0 1-5.7-5.7l1.5-1.5 1.4 1.4-1.5 1.5a2 2 0 0 0 2.9 2.9l3-3a2 2 0 0 0 0-2.9z"/></svg>www.brightwayretro.com</li>
      </ul>
    </div>
  </section>

  <section class="card card--back">
    <div class="brand">
      <span class="brand__mark" aria-hidden="true"></span>
      <span class="brand__name">Brightway Retrofit Co.</span>
    </div>
  </section>
</main>
</body>
</html>
```